Brintel Works - Fast, Efficient and Gas Mainteance for Domestic, Commercial and Industrial clients

We are in the process of purchasing a new business and would like to get a new logo and business card.
Business is a gas maintenance business that also does new gas installations.
Has been established since 1988.
Services include:
Install all types of gas appliances & equipment inc. hot water units
Maintain / repair / replace all types of gas appliances & equipment

Target Market(s)

Domestic, Commercial and Industrial clients

Industry/Entity Type

Business

Contact Information for Business Card

admin@brintelworks.com.au
07 3918 4726
Brintel Works PTY LTD

Logo Text

Gas Fitting & Plumbing Maintenance Specialists

Font styles to use
Sans Serif

Requirements
Must have
• Logo
• Business name, contact number, email address, web address
• Domestic | Commercial | Industrial Est Since 1988
Nice to have
• Possibly a black card with a flame logo to one side
Should not have
• Spelling errors

```html
<!DOCTYPE html>
<html lang="en">
<head>
<meta charset="utf-8">
<title>Brintel Works PTY LTD – Business Card</title>
<link href="https://fonts.googleapis.com/css2?family=PT+Serif:wght@700&family=Open+Sans:wght@400;600;700&family=Great+Vibes&display=swap" rel="stylesheet">
<style>
  :root {
    --backdrop: #e9e7e3;
    --card: #f7f7f7;
    --brand-red: #e0533b;
    --swoosh-grey: #b3b3b3;
    --mark-grey: #dcdcdc;
    --slate: #3d4250;
    --ink: #1a1a1a;
    --muted: #777a80;
  }
  * { box-sizing: border-box; margin: 0; padding: 0; }
  html, body {
    width: 1200px; height: 902px; overflow: hidden;
    background: var(--backdrop);
  }
  .card {
    position: absolute; left: 60px; top: 142px;
    width: 1080px; height: 617px;
    background: var(--card);
    box-shadow: 0 10px 30px rgba(0,0,0,.18);
    overflow: hidden;
  }
  .card-art { position: absolute; inset: 0; }
  .brand-mark {
    position: absolute; left: 70px; top: 150px;
    width: 230px; height: 230px; border-radius: 50%;
    background: var(--mark-grey);
  }
  .brand-block { position: absolute; left: 250px; top: 120px; }
  .brand-name {
    font-family: "PT Serif", serif; font-weight: 700;
    font-size: 48px; color: var(--brand-red);
    letter-spacing: .5px; white-space: nowrap;
  }
  .brand-name .entity {
    font-family: "Open Sans", sans-serif; font-weight: 700;
    font-size: 10px; color: var(--slate);
    vertical-align: super; margin-left: 6px; letter-spacing: 1px;
  }
  .tagline {
    font-family: "Open Sans", sans-serif; font-weight: 700;
    font-size: 27px; color: var(--slate); margin-top: 2px; white-space: nowrap;
  }
  .sectors {
    display: flex; align-items: baseline; gap: 18px; margin-top: 4px;
  }
  .sectors .markets {
    font-family: "Open Sans", sans-serif; font-size: 13px; color: var(--muted);
  }
  .sectors .established {
    font-family: "Great Vibes", cursive; font-size: 26px; color: #8a8d92;
  }
  .divider {
    position: absolute; left: 0; top: 318px;
    width: 580px; height: 3px; background: var(--brand-red);
  }
  .contact {
    position: absolute; right: 270px; top: 290px;
    text-align: right;
    font-family: "Open Sans", sans-serif; font-size: 29px; color: var(--ink);
    line-height: 1.35;
  }
  .contact .phone { margin-bottom: 36px; }
  .contact-icons {
    position: absolute; left: 838px; top: 196px;
    display: flex; flex-direction: column; gap: 14px;
  }
  .contact-icons svg { display: block; width: 30px; height: 30px; }
</style>
</head>
<body>
  <main class="card">
    <svg class="card-art" viewBox="0 0 1080 617" aria-hidden="true">
      <path fill="var(--brand-red)" d="M900,0 L1080,0 L1080,617 L960,617 C945,400 930,200 900,0 Z"/>
      <path fill="var(--swoosh-grey)" d="M610,0 L900,0 C912,90 920,160 930,220 C860,95 760,30 610,0 Z"/>
      <path fill="var(--swoosh-grey)" d="M930,220 C952,360 960,500 960,617 L905,617 C915,470 900,330 840,245 C880,255 912,242 930,220 Z"/>
    </svg>

    <div class="brand-mark" role="img" aria-label="Faint company mark area"></div>

    <header class="brand-block">
      <h1 class="brand-name">BRINTEL WORKS<span class="entity">PTY LTD</span></h1>
      <p class="tagline">Gas fitting &amp; Plumbing Specialists</p>
      <p class="sectors">
        <span class="markets">Domestic | Commercial | Industrial</span>
        <span class="established">Est Since 1988</span>
      </p>
    </header>

    <div class="divider"></div>

    <div class="contact-icons">
      <svg viewBox="0 0 30 30" aria-label="Phone" role="img">
        <rect width="30" height="30" fill="var(--ink)"/>
        <path fill="#fff" d="M10 7 L13 7 L14 11 L12 13 C13 16 15 18 17 19 L19 17 L23 18 L23 21 C23 22 22 23 21 23 C14 22 8 16 7 9 C7 8 8 7 10 7 Z"/>
      </svg>
      <svg viewBox="0 0 30 30" aria-label="Email" role="img">
        <rect width="30" height="30" fill="var(--ink)"/>
        <rect x="6" y="9" width="18" height="12" fill="none" stroke="#fff" stroke-width="2"/>
        <path d="M6 9 L15 16 L24 9" fill="none" stroke="#fff" stroke-width="2"/>
      </svg>
      <svg viewBox="0 0 30 30" aria-label="Website" role="img">
        <rect width="30" height="30" fill="var(--ink)"/>
        <circle cx="15" cy="15" r="8" fill="none" stroke="#fff" stroke-width="2"/>
        <ellipse cx="15" cy="15" rx="3.5" ry="8" fill="none" stroke="#fff" stroke-width="1.5"/>
        <line x1="7" y1="15" x2="23" y2="15" stroke="#fff" stroke-width="1.5"/>
      </svg>
    </div>

    <address class="contact">
      <p class="phone">07 3918 4726</p>
      <p class="email">admin@brintelworks.com.au</p>
      <p class="web">www.brintelworks.com.au</p>
    </address>
  </main>
</body>
</html>
```